Construction company that specializes in roofing and siding

https://maplecrestbuild.example/featured-projects/

https://www.bramwickhomesllc.example/#

https://www.tallgrovecontractors.example/residential-siding-services/

Please model a website after these examples
I posted a doc that has some content to get you started. I will upload more content and photos as the site progresses.

Coded - Design and coding required

5+ page

```html
<!DOCTYPE html>
<html lang="en">
<head>
<meta charset="utf-8">
<title>Stonebridge Construction — Home Page Concepts</title>
<link rel="stylesheet" href="https://fonts.googleapis.com/css2?family=Krona+One&family=Inter:wght@400;500;600;700&display=swap">
<style>
:root{
  --ink:#1b1b1b;
  --text:#3a3a3a;
  --muted:#777;
  --dark:#555555;
  --bar:#434343;
  --light:#f3f3f3;
  --paper:#ffffff;
  --line:#d8d8d8;
  --star:#f2a93b;
  --sky:#c9d4e0;
  --roof:#3b3e44;
}
*{box-sizing:border-box;margin:0;padding:0}
html,body{width:692px;height:1200px;overflow:hidden;background:var(--paper)}
body{font-family:"Inter",sans-serif;color:var(--text)}
.stage{position:absolute;left:4.75px;top:0;width:1456px;height:2560px;transform:scale(.46875);transform-origin:0 0;background:var(--paper)}
.concept-title{position:absolute;top:18px;font-family:"Krona One",sans-serif;font-size:14px;color:var(--ink);letter-spacing:.5px;text-align:center}
.page{position:absolute;top:48px;height:2428px;background:var(--paper);box-shadow:0 0 6px rgba(0,0,0,.12);overflow:hidden}
.page--v1{left:139px;width:558px}
.page--v2{left:742px;width:575px}
.sec{position:absolute;left:0;right:0}
.display{font-family:"Krona One",sans-serif;color:var(--ink);text-transform:uppercase;line-height:1.12}
.eyebrow{font-family:"Krona One",sans-serif;font-size:5px;letter-spacing:1px;text-transform:uppercase;color:var(--ink)}
.on-dark,.on-dark .display,.on-dark .eyebrow{color:#fff}
.photo{border-radius:3px}
.btn{display:inline-block;font-size:5.5px;font-weight:700;text-transform:uppercase;padding:6px 11px;border-radius:2px;letter-spacing:.2px;white-space:nowrap}
.btn--solid{background:var(--ink);color:#fff}
.btn--grey{background:var(--dark);color:#fff}
.btn--ghost{border:1px solid #fff;color:#fff}
/* top bar */
.topbar{top:0;height:22px;background:var(--bar);color:#fff;font-size:5.8px;display:flex;align-items:center;padding:0 40px;gap:12px}
.topbar .social{margin-left:auto;display:flex;gap:6px}
.dot{width:6px;height:6px;border-radius:50%;background:#fff;display:inline-block}
.ico{display:inline-flex;align-items:center;gap:4px}
/* nav */
.nav{height:50px;display:flex;align-items:center;padding:0 40px}
.brand{display:flex;align-items:center;gap:6px}
.brand-mark{width:22px;height:22px;border-radius:50%;background:var(--dark)}
.brand-name{font-family:"Krona One",sans-serif;font-size:8px;color:var(--ink);line-height:1.1;text-transform:uppercase}
.menu{margin-left:auto;display:flex;align-items:center;gap:14px;font-size:6.5px;color:var(--ink)}
/* services */
.cards{position:absolute;display:flex;gap:17px}
.svc-card{border:1px solid #777;background:var(--dark);color:#fff}
.svc-card h4{font-size:8px;font-weight:600;margin:8px 10px 5px}
.svc-card li{list-style:none;font-size:5.8px;margin:0 10px 5px;color:#eee}
.svc-card li::before{content:"›";margin-right:4px}
.svc-card .btn{margin:10px 10px 0}
/* testimonials */
.review{background:#fff;box-shadow:0 1px 5px rgba(0,0,0,.15);padding:10px;color:var(--text);font-size:5.8px;line-height:1.45}
.review-head{display:flex;align-items:center;gap:5px;margin-bottom:6px;font-weight:700;color:var(--ink);font-size:6.5px}
.avatar{width:16px;height:16px;border-radius:50%;background:#b7a99a}
.review-foot{display:flex;justify-content:space-between;margin-top:10px;font-size:5px}
.stars{color:var(--star);letter-spacing:1px}
.pager{position:absolute;left:0;right:0;text-align:center;font-size:14px;color:var(--ink);letter-spacing:6px}
/* team */
.team{position:absolute;display:flex}
.member{text-align:center}
.member strong{display:block;font-size:7.5px;color:var(--ink);margin-top:10px}
.member span{display:block;font-size:5.5px;font-style:italic;color:var(--muted)}
.lede{position:absolute;left:0;right:0;text-align:center;font-size:6.2px;line-height:1.6;color:var(--text)}
/* blog */
.posts{position:absolute;display:flex}
.post time{display:block;font-size:5px;font-weight:700;color:#fff;margin-top:7px}
.post h5{font-size:8px;font-weight:600;color:#fff;line-height:1.3;margin-top:2px}
.post .photo{border:1px solid #888}
/* footer */
.footer{color:var(--text)}
.f-about{position:absolute;font-size:6.2px;line-height:1.6}
.f-col{position:absolute}
.f-col h6{font-family:"Krona One",sans-serif;font-size:5.5px;color:var(--ink);margin-bottom:10px}
.f-col li{list-style:none;font-size:6px;margin-bottom:6px}
.f-social{position:absolute;display:flex;gap:6px}
.f-social i{width:14px;height:14px;border:1px solid var(--ink);border-radius:50%;display:block}
.f-nav{position:absolute;left:0;right:0;height:22px;border-top:1px solid var(--line);border-bottom:1px solid var(--line);display:flex;justify-content:center;font-size:5.5px;text-transform:uppercase;color:var(--ink);letter-spacing:.5px}
.f-nav span{padding:0 13px;border-right:1px solid var(--line);display:flex;align-items:center}
.f-nav span:last-child{border-right:0}
.f-legal{position:absolute;left:40px;right:40px;display:flex;justify-content:space-between;font-size:5px}
</style>
</head>
<body>
<div class="stage">

<div class="concept-title" style="left:139px;width:558px">Home Page V.01</div>
<div class="concept-title" style="left:742px;width:575px">Home Page V.02</div>

<!-- ================= V.01 ================= -->
<main class="page page--v1">
  <div class="sec topbar"><span class="ico">☎ 1800-555-010</span><span class="ico">✉ info@stonebridgebuild.example</span><span class="social"><i class="dot"></i><i class="dot"></i><i class="dot"></i></span></div>
  <header class="sec nav" style="top:22px">
    <div class="brand"><span class="brand-mark"></span><span class="brand-name">Stonebridge<br>Construction</span></div>
    <nav class="menu"><span>Home</span><span>About</span><span>What we do</span><span>Blog</span><span>Contact</span><span class="btn btn--solid">Get free inspection →</span></nav>
  </header>

  <section class="sec" style="top:72px;height:300px">
    <div role="img" aria-label="Stone-faced house with dark shingle roof under a cloudy sky" style="position:absolute;inset:0 0 0 0;background:linear-gradient(180deg,#6f7884 0%,#8c8f92 30%,#4d4f53 55%,#a79d8c 100%);clip-path:polygon(0 0,100% 0,100% 78%,50% 100%,0 78%)"></div>
    <div style="position:absolute;left:40px;top:55px">
      <div class="eyebrow" style="color:#fff;font-size:7px">Stonebridge Construction</div>
      <h1 class="display" style="color:#fff;font-size:14.5px;margin-top:6px;line-height:1.5">Is your source for<br>roofing and siding in<br>Minnesota</h1>
      <span class="btn btn--ghost" style="margin-top:14px">Contact us →</span>
    </div>
  </section>

  <section class="sec" style="top:372px;height:308px">
    <div role="img" aria-label="Roofers installing standing seam metal roof panels" class="photo" style="position:absolute;left:40px;top:48px;width:170px;height:210px;background:linear-gradient(160deg,#d7dde4,#5d6168 55%,#2e3034)"></div>
    <div style="position:absolute;left:257px;top:76px;width:262px">
      <div class="eyebrow">About</div>
      <h2 class="display" style="font-size:13px;margin-top:2px">Stonebridge Construction</h2>
      <p style="font-size:6.5px;font-weight:600;color:var(--ink);margin:8px 0 7px">From humble beginnings</p>
      <p style="font-size:5.8px;line-height:1.65">In 2016 Owen Hale started helping people with their home improvement projects. His very first job was installing window trim for a wonderful homeowner in Forest lake MN. He did his best work and made sure he treated his first customer like family. Afterall, his first customer was Rosa Hale, his Mom.</p>
      <span class="btn btn--solid" style="margin-top:13px">Get free inspection →</span>
    </div>
  </section>

  <section class="sec on-dark" style="top:680px;height:305px;background:var(--dark)">
    <div style="text-align:center;margin-top:33px"><div class="eyebrow">Services</div><h2 class="display" style="font-size:13px;margin-top:2px">What we do</h2></div>
    <div class="cards" style="left:40px;top:70px">
      <article class="svc-card" style="width:148px;height:205px"><div role="img" aria-label="Roofer on a metal roof" style="height:94px;background:linear-gradient(180deg,#c6d3e2,#4a4c52)"></div><h4>Roofing</h4><ul><li>Architectural shingles</li><li>Standing seam steel roofing</li><li>Agricultural steel roofing</li></ul><span class="btn btn--ghost">Learn more →</span></article>
      <article class="svc-card" style="width:148px;height:205px"><div role="img" aria-label="Worker fitting siding under roof eaves" style="height:94px;background:linear-gradient(180deg,#7a6e62,#4a5a78)"></div><h4>Siding</h4><ul><li>Vinyl siding</li><li>Ridgeline steel siding</li><li>TrueGrain engineered siding</li></ul><span class="btn btn--ghost">Learn more →</span></article>
      <article class="svc-card" style="width:148px;height:205px"><div role="img" aria-label="Repair worker with a power drill" style="height:94px;background:linear-gradient(180deg,#e4e9ee,#8a8e94)"></div><h4>Repair</h4><ul><li>Missing shingles</li><li>Leaking roof</li><li>Add vents</li></ul><span class="btn btn--ghost">Learn more →</span></article>
    </div>
  </section>

  <section class="sec" style="top:985px;height:325px">
    <div style="text-align:center;margin-top:18px"><div class="eyebrow">Featured work</div><h2 class="display" style="font-size:13px;margin-top:2px">Best works all time</h2></div>
    <div role="img" aria-label="Dark tiled roof with brick chimney" class="photo" style="position:absolute;left:40px;top:52px;width:255px;height:224px;background:linear-gradient(170deg,#8fb3d8 0%,#9fb5cc 25%,#2d2f33 45%,#3a3c40 100%)"></div>
    <div role="img" aria-label="Gutter and soffit against the sky" class="photo" style="position:absolute;left:305px;top:52px;width:213px;height:107px;background:linear-gradient(160deg,#7aa3cf,#d8dde2 55%,#c7b08d)"></div>
    <div role="img" aria-label="Bright interior with large windows" class="photo" style="position:absolute;left:305px;top:168px;width:213px;height:108px;background:linear-gradient(90deg,#e8e8e6,#f4f4f2 60%,#b8c2a0)"></div>
    <div style="position:absolute;left:0;right:0;top:284px;text-align:center"><span class="btn btn--solid">View all →</span></div>
  </section>

  <section class="sec" style="top:1310px;height:285px">
    <div style="position:absolute;left:0;right:0;top:0;height:210px;background:var(--dark)"></div>
    <div class="on-dark" style="position:absolute;left:0;right:0;top:40px;text-align:center"><div class="eyebrow">Featured work</div><h2 class="display" style="font-size:12.5px;margin-top:3px">We're trusted by<br>our clients</h2></div>
    <div class="cards" style="left:40px;top:155px;gap:12px">
      <article class="review" style="width:151px"><div class="review-head"><span class="avatar"></span>Marcus Reed</div>Lorem ipsum dolor sit amet, consectetur adipiscing elit. Nulla odio massa, dapibus in congue ac, conditum eget ex. Integer tincidunt tortor eu libero pulvinar<div class="review-foot"><span>2 days ago</span><span class="stars">★★★★★</span></div></article>
      <article class="review" style="width:152px"><div class="review-head"><span class="avatar"></span>Lena Ortiz</div>Lorem ipsum dolor sit amet, consectetur adipiscing elit. Nulla odio massa, dapibus in congue ac, conditum eget ex. Integer tincidunt tortor eu libero pulvinar<div class="review-foot"><span>1 days ago</span><span class="stars">★★★★★</span></div></article>
      <article class="review" style="width:151px"><div class="review-head"><span class="avatar"></span>Marcus Reed</div>Lorem ipsum dolor sit amet, consectetur adipiscing elit. Nulla odio massa, dapibus in congue ac, conditum eget ex. Integer tincidunt tortor eu libero pulvinar<div class="review-foot"><span>2days ago</span><span class="stars">★★★★★</span></div></article>
    </div>
    <div class="pager" style="top:271px">⟵⟶</div>
  </section>

  <section class="sec" style="top:1595px;height:307px;background:#f8f8f8">
    <h2 class="display" style="position:absolute;left:0;right:0;top:43px;text-align:center;font-size:12.5px">Our experts<br>team members</h2>
    <p class="lede" style="top:78px">Phasellus molestie aliquet libero, nec vestibulum lacus fermentum euismod. Nulla<br>ut lorem arcu. Aliquam ullamcorper auctor lobortis.</p>
    <div class="team" style="left:40px;top:117px;gap:31px">
      <div class="member"><div role="img" aria-label="Team member in hard hat" style="width:96px;height:110px;background:linear-gradient(180deg,#d9dde2,#b9b3aa)"></div><strong>Theo Grant</strong><span>Seniour Member</span></div>
      <div class="member"><div role="img" aria-label="Team member in safety vest" style="width:97px;height:110px;background:linear-gradient(180deg,#8a6b48,#c9cd5a)"></div><strong>Nora Grant</strong><span>Seniour Member</span></div>
      <div class="member"><div role="img" aria-label="Team member in safety vest" style="width:96px;height:110px;background:linear-gradient(180deg,#6a6e74,#3c6fb8 60%,#c8d95a)"></div><strong>Theo Grant</strong><span>Seniour Member</span></div>
      <div class="member"><div role="img" aria-label="Team member in hard hat" style="width:96px;height:110px;background:linear-gradient(180deg,#5a5f66,#2f3a55 60%,#c7d05a)"></div><strong>Theo Grant</strong><span>Seniour Member</span></div>
    </div>
  </section>

  <section class="sec on-dark" style="top:1902px;height:305px;background:var(--dark)">
    <div style="position:absolute;left:40px;top:51px"><div class="eyebrow">Blog &amp; articles</div><h2 class="display" style="font-size:13px;margin-top:2px">Our latest blog</h2></div>
    <span class="btn btn--ghost" style="position:absolute;right:40px;top:56px;padding:6px 16px">View all →</span>
    <div class="posts" style="left:40px;top:95px;gap:11px">
      <article class="post" style="width:151px"><div role="img" aria-label="Worker drilling on a metal roof" class="photo" style="height:117px;background:linear-gradient(160deg,#8fb0d0,#b89a5a 45%,#3d4046)"></div><time>2 June 2024</time><h5>Suspendisse commodo sollicitudin volutpat dictum</h5></article>
      <article class="post" style="width:151px"><div role="img" aria-label="Roofer on a standing seam roof" class="photo" style="height:117px;background:linear-gradient(160deg,#c9cfd6,#5a5e66 50%,#34373c)"></div><time>2 June 2024</time><h5>Suspendisse commodo sollicitudin volutpat dictum</h5></article>
      <article class="post" style="width:151px"><div role="img" aria-label="Pressure washing a roof gutter" class="photo" style="height:117px;background:linear-gradient(160deg,#6aa06a,#4d7fb2 45%,#3c4048)"></div><time>2 June 2024</time><h5>Suspendisse commodo sollicitudin volutpat dictum</h5></article>
    </div>
  </section>

  <footer class="sec footer" style="top:2207px;height:221px">
    <div class="brand" style="position:absolute;left:40px;top:28px"><span class="brand-mark"></span><span class="brand-name">Stonebridge<br>Construction</span></div>
    <p class="f-about" style="left:40px;top:70px;width:135px">In 2016 Owen Hale started helping people with their home improvement projects. His very first job was installing window trim for a wonderful</p>
    <div class="f-social" style="left:68px;top:126px"><i></i><i></i><i></i></div>
    <div class="f-col" style="left:213px;top:37px"><h6>Services</h6><ul><li>Roofing</li><li>Siding</li><li>Gutters</li><li>Windows</li><li>Repair</li></ul></div>
    <div class="f-col" style="left:299px;top:37px"><h6>Useful links</h6><ul><li>Privacy Policy</li><li>Terms &amp; Condition</li><li>Sitemap</li><li>Other</li></ul></div>
    <div class="f-col" style="left:407px;top:37px"><h6>Contact us</h6><ul><li>hello@stonebridgebuild.example</li><li>1800 555 010</li></ul></div>
    <nav class="f-nav" style="top:158px"><span>Home</span><span>About</span><span>What we do</span><span>Blog</span><span>Contact</span></nav>
    <div class="f-legal" style="top:200px"><span>© 2024 <b>Stonebridge Construction.</b> All right reserved</span><span>July 01, 2024. Layout_4</span></div>
  </footer>
</main>

<!-- ================= V.02 ================= -->
<main class="page page--v2">
  <div class="sec topbar" style="height:23px;padding:0 41px"><span class="ico">☎ 1800-555-010</span><span class="ico">✉ info@stonebridgebuild.example</span><span class="social"><i class="dot"></i><i class="dot"></i><i class="dot"></i></span></div>
  <section class="sec" style="top:23px;height:292px">
    <header class="nav" style="padding:0 41px">
      <div class="brand"><span class="brand-mark"></span><span class="brand-name">Stonebridge<br>Construction</span></div>
      <nav class="menu"><span>Home</span><span>About</span><span>What we do</span><span>Blog</span><span>Contact</span><span class="btn btn--grey">Get free inspection →</span></nav>
    </header>
    <div style="position:absolute;left:41px;top:88px">
      <h1 class="display" style="font-size:19px;line-height:1.3">Get<br>20 years of<br>service</h1>
      <p style="font-size:8px;color:var(--ink);margin-top:8px">Out of an architectural shingle roof</p>
      <span class="btn btn--grey" style="margin-top:14px">Contact us →</span>
    </div>
    <div role="img" aria-label="Brick house with dark tiled roof" class="photo" style="position:absolute;left:290px;top:40px;width:238px;height:248px;background:linear-gradient(170deg,#d6d8db,#34373c 40%,#b4553a 75%,#6b6e73)"></div>
  </section>

  <section class="sec" style="top:315px;height:317px;background:var(--light)">
    <div role="img" aria-label="Roofers installing standing seam metal roof panels" class="photo" style="position:absolute;left:44px;top:61px;width:231px;height:205px;background:linear-gradient(160deg,#d7dde4,#5d6168 50%,#2e3034)"></div>
    <div style="position:absolute;left:294px;top:87px;width:240px">
      <div class="eyebrow">About</div>
      <h2 class="display" style="font-size:13px;margin-top:3px">Stonebridge<br>Construction</h2>
      <p style="font-size:6px;line-height:1.65;margin-top:9px">In 2016 Owen Hale started helping people with their home improvement projects. His very first job was installing window trim for a wonderful homeowner in Forest lake MN. He did his best work and made sure he treated his first customer like family. Afterall, his first customer was Rosa Hale, his Mom.</p>
      <span class="btn btn--grey" style="margin-top:11px">Get free inspection →</span>
    </div>
  </section>

  <section class="sec on-dark" style="top:632px;height:316px;background:var(--dark)">
    <div style="text-align:center;margin-top:33px"><div class="eyebrow">Services</div><h2 class="display" style="font-size:13px;margin-top:2px">What we do</h2></div>
    <div class="cards" style="left:41px;top:72px">
      <article class="svc-card" style="width:153px;height:213px"><div role="img" aria-label="Roofer on a metal roof" style="height:97px;background:linear-gradient(180deg,#c6d3e2,#4a4c52)"></div><h4>Roofing</h4><ul><li>Architectural shingles</li><li>Standing seam steel roofing</li><li>Agricultural steel roofing</li></ul><span class="btn btn--ghost">Learn more →</span></article>
      <article class="svc-card" style="width:153px;height:213px"><div role="img" aria-label="Worker fitting siding under roof eaves" style="height:97px;background:linear-gradient(180deg,#7a6e62,#4a5a78)"></div><h4>Siding</h4><ul><li>Vinyl siding</li><li>Ridgeline steel siding</li><li>TrueGrain engineered siding</li></ul><span class="btn btn--ghost">Learn more →</span></article>
      <article class="svc-card" style="width:153px;height:213px"><div role="img" aria-label="Repair worker with a power drill" style="height:97px;background:linear-gradient(180deg,#e4e9ee,#8a8e94)"></div><h4>Repair</h4><ul><li>Missing shingles</li><li>Leaking roof</li><li>Add vents</li></ul><span class="btn btn--ghost">Learn more →</span></article>
    </div>
  </section>

  <section class="sec" style="top:948px;height:334px">
    <div style="text-align:center;margin-top:18px"><div class="eyebrow">Featured work</div><h2 class="display" style="font-size:13px;margin-top:2px">Best works all time</h2></div>
    <div role="img" aria-label="Dark tiled roof with brick chimney" class="photo" style="position:absolute;left:41px;top:52px;width:263px;height:232px;background:linear-gradient(170deg,#8fb3d8 0%,#9fb5cc 25%,#2d2f33 45%,#3a3c40 100%)"></div>
    <div role="img" aria-label="Gutter and soffit against the sky" class="photo" style="position:absolute;left:314px;top:52px;width:220px;height:112px;background:linear-gradient(160deg,#7aa3cf,#d8dde2 55%,#c7b08d)"></div>
    <div role="img" aria-label="Bright interior with large windows" class="photo" style="position:absolute;left:314px;top:172px;width:220px;height:112px;background:linear-gradient(90deg,#e8e8e6,#f4f4f2 60%,#b8c2a0)"></div>
    <div style="position:absolute;left:0;right:0;top:292px;text-align:center"><span class="btn btn--grey" style="padding:6px 16px">View all →</span></div>
  </section>

  <section class="sec" style="top:1282px;height:295px;background:#f8f8f8">
    <div style="position:absolute;left:0;right:0;top:0;height:218px;background:var(--dark)"></div>
    <div class="on-dark" style="position:absolute;left:0;right:0;top:44px;text-align:center"><div class="eyebrow">Featured work</div><h2 class="display" style="font-size:12.5px;margin-top:3px">We're trusted by<br>our clients</h2></div>
    <div class="cards" style="left:41px;top:158px;gap:12px">
      <article class="review" style="width:156px"><div class="review-head"><span class="avatar"></span>Marcus Reed</div>Lorem ipsum dolor sit amet, consectetur adipiscing elit. Nulla odio massa, dapibus in congue ac, conditum eget ex. Integer tincidunt tortor eu libero pulvinar<div class="review-foot"><span>2 days ago</span><span class="stars">★★★★★</span></div></article>
      <article class="review" style="width:156px"><div class="review-head"><span class="avatar"></span>Lena Ortiz</div>Lorem ipsum dolor sit amet, consectetur adipiscing elit. Nulla odio massa, dapibus in congue ac, conditum eget ex. Integer tincidunt tortor eu libero pulvinar<div class="review-foot"><span>1 days ago</span><span class="stars">★★★★★</span></div></article>
      <article class="review" style="width:157px"><div class="review-head"><span class="avatar"></span>Marcus Reed</div>Lorem ipsum dolor sit amet, consectetur adipiscing elit. Nulla odio massa, dapibus in congue ac, conditum eget ex. Integer tincidunt tortor eu libero pulvinar<div class="review-foot"><span>2days ago</span><span class="stars">★★★★★</span></div></article>
    </div>
    <div class="pager" style="top:283px">⟵⟶</div>
  </section>

  <section class="sec" style="top:1577px;height:315px;background:#f8f8f8">
    <h2 class="display" style="position:absolute;left:0;right:0;top:43px;text-align:center;font-size:12.5px">Our experts<br>team members</h2>
    <p class="lede" style="top:78px">Phasellus molestie aliquet libero, nec vestibulum lacus fermentum euismod. Nulla<br>ut lorem arcu. Aliquam ullamcorper auctor lobortis.</p>
    <div class="team" style="left:41px;top:120px;gap:32px">
      <div class="member"><div role="img" aria-label="Team member in hard hat" style="width:99px;height:113px;background:linear-gradient(180deg,#d9dde2,#b9b3aa)"></div><strong>Theo Grant</strong><span>Seniour Member</span></div>
      <div class="member"><div role="img" aria-label="Team member in safety vest" style="width:99px;height:113px;background:linear-gradient(180deg,#8a6b48,#c9cd5a)"></div><strong>Nora Grant</strong><span>Seniour Member</span></div>
      <div class="member"><div role="img" aria-label="Team member in safety vest" style="width:99px;height:113px;background:linear-gradient(180deg,#6a6e74,#3c6fb8 60%,#c8d95a)"></div><strong>Theo Grant</strong><span>Seniour Member</span></div>
      <div class="member"><div role="img" aria-label="Team member in hard hat" style="width:99px;height:113px;background:linear-gradient(180deg,#5a5f66,#2f3a55 60%,#c7d05a)"></div><strong>Theo Grant</strong><span>Seniour Member</span></div>
    </div>
  </section>

  <section class="sec on-dark" style="top:1892px;height:316px;background:var(--dark)">
    <div style="position:absolute;left:41px;top:51px"><div class="eyebrow">Blog &amp; articles</div><h2 class="display" style="font-size:13px;margin-top:2px">Our latest blog</h2></div>
    <span class="btn btn--ghost" style="position:absolute;right:41px;top:58px;padding:6px 16px">View all →</span>
    <div class="posts" style="left:41px;top:100px;gap:11px">
      <article class="post" style="width:157px"><div role="img" aria-label="Worker drilling on a metal roof" class="photo" style="height:118px;background:linear-gradient(160deg,#8fb0d0,#b89a5a 45%,#3d4046)"></div><time>2 June 2024</time><h5>Suspendisse commodo sollicitudin volutpat dictum</h5></article>
      <article class="post" style="width:157px"><div role="img" aria-label="Roofer on a standing seam roof" class="photo" style="height:118px;background:linear-gradient(160deg,#c9cfd6,#5a5e66 50%,#34373c)"></div><time>2 June 2024</time><h5>Suspendisse commodo sollicitudin volutpat dictum</h5></article>
      <article class="post" style="width:157px"><div role="img" aria-label="Pressure washing a roof gutter" class="photo" style="height:118px;background:linear-gradient(160deg,#6aa06a,#4d7fb2 45%,#3c4048)"></div><time>2 June 2024</time><h5>Suspendisse commodo sollicitudin volutpat dictum</h5></article>
    </div>
  </section>

  <footer class="sec footer" style="top:2208px;height:220px">
    <div class="brand" style="position:absolute;left:41px;top:28px"><span class="brand-mark"></span><span class="brand-name">Stonebridge<br>Construction</span></div>
    <p class="f-about" style="left:41px;top:70px;width:138px">In 2016 Owen Hale started helping people with their home improvement projects. His very first job was installing window trim for a wonderful</p>
    <div class="f-social" style="left:70px;top:126px"><i></i><i></i><i></i></div>
    <div class="f-col" style="left:219px;top:37px"><h6>Services</h6><ul><li>Roofing</li><li>Siding</li><li>Gutters</li><li>Windows</li><li>Repair</li></ul></div>
    <div class="f-col" style="left:308px;top:37px"><h6>Useful links</h6><ul><li>Privacy Policy</li><li>Terms &amp; Condition</li><li>Sitemap</li><li>Other</li></ul></div>
    <div class="f-col" style="left:419px;top:37px"><h6>Contact us</h6><ul><li>hello@stonebridgebuild.example</li><li>1800 555 010</li></ul></div>
    <nav class="f-nav" style="top:162px"><span>Home</span><span>About</span><span>What we do</span><span>Blog</span><span>Contact</span></nav>
    <div class="f-legal" style="left:41px;right:41px;top:200px"><span>© 2024 <b>Stonebridge Construction.</b> All right reserved</span><span>July 01, 2024. Layout_4</span></div>
  </footer>
</main>

</div>
</body>
</html>
```